Membership Certificate for Chamber of Commerce Member

I am looking for a certificate to present to Chamber of Commerce Members that showcases their annual membership. The certificate will be placed in frame. I have attached a sample image of the frame from another Chamber of Commerce. I have also attached a proof of the frame that shows our logo at the top and the words "Working Together for a Stronger Community" at the bottom. The certificate should be 7" wide by 5" high. It should say Proud Chamber Member and the year, 2022. I have attached two versions of our logo. I am open to any further suggestions.

Target Market(s)

Business owners/managers

Requirements
Must have
• Year, Proud Chamber Member
Nice to have
• Colors and design that fit our logo and branding. Our website is www.thebraxleyguild.com.

```html
<!DOCTYPE html>
<html lang="en">
<head>
<meta charset="utf-8">
<title>Braxley Guild – Annual Membership Certificate</title>
<link rel="stylesheet" href="https://fonts.googleapis.com/css2?family=Marcellus&family=Montserrat:wght@500;600;700&family=Crimson+Text:wght@600;700&display=swap">
<style>
  :root {
    --page: #f4f4f5;
    --paper: #ffffff;
    --navy: #1c2a7a;
    --sky: #1e8fd0;
    --slate: #656b70;
    --green: #1e8a2c;
    --orange: #ef8a2a;
    --band-start: #4a6ff0;
    --band-end: #2453b8;
    --edge: #c9cbce;
  }
  * { margin: 0; padding: 0; box-sizing: border-box; }
  html, body { width: 706px; height: 1200px; overflow: hidden; }
  body { background: var(--page); position: relative; font-family: "Montserrat", sans-serif; }

  .certificate {
    position: absolute;
    width: 610px; height: 435px;
    background: var(--paper);
    box-shadow: 0 2px 8px rgba(0,0,0,.18);
    overflow: hidden;
    transform-origin: top left;
  }
  .certificate--primary { left: 48px; top: 82px; }
  .certificate--secondary { left: 74px; top: 785px; transform: scale(0.915); }

  .brand { position: absolute; top: 20px; left: 0; right: 0; text-align: center; }
  .brand-dot { display: block; width: 30px; height: 30px; border-radius: 50%; background: var(--sky); margin: 0 auto 6px; }
  .brand-name { font-weight: 700; font-size: 13px; color: var(--navy); letter-spacing: .2px; line-height: 1; }
  .brand-sub { font-weight: 500; font-size: 7px; color: var(--navy); letter-spacing: 1.4px; margin-top: 2px; }

  .texture-band {
    position: absolute; top: 90px; left: 0; width: 610px; height: 66px;
    background: linear-gradient(90deg, var(--orange) 0%, #3f9fd8 10%, #4aa6dc 20%, #e8e9eb 38%, #f2f2f3 70%, #4aa6dc 88%, var(--orange) 100%);
  }
  .band-edge { position: absolute; top: 150px; left: 0; width: 610px; height: 30px; }

  .title-accent {
    position: absolute; top: 178px; width: 40px; height: 56px;
  }
  .title-accent--left { left: 112px; background: linear-gradient(90deg, rgba(239,138,42,0), rgba(239,138,42,.35)); }
  .title-accent--right { left: 458px; background: linear-gradient(90deg, rgba(30,143,208,.35), rgba(30,143,208,0)); }

  .title {
    position: absolute; top: 162px; left: 0; right: 0; text-align: center;
    font-family: "Marcellus", serif; font-size: 64px; color: var(--slate); line-height: 1;
  }
  .subtitle {
    position: absolute; top: 226px; left: 0; right: 0; text-align: center;
    font-weight: 600; font-size: 12.5px; color: var(--sky); letter-spacing: .3px;
  }
  .given-to {
    position: absolute; top: 258px; left: 0; right: 0;
    display: flex; align-items: center; justify-content: center; gap: 8px;
    font-weight: 500; font-size: 10.5px; color: var(--navy);
  }
  .given-to::before, .given-to::after { content: ""; width: 62px; height: 3px; background: linear-gradient(90deg, transparent, #8e9297); }
  .given-to::after { transform: scaleX(-1); }
  .recipient {
    position: absolute; top: 272px; left: 0; right: 0; text-align: center;
    font-family: "Crimson Text", serif; font-weight: 700; font-size: 21px; color: var(--green); letter-spacing: .2px;
  }

  .signature { position: absolute; top: 309px; width: 100px; text-align: center; }
  .signature--left { left: 46px; }
  .signature--right { left: 468px; }
  .signature-line { border-top: 1.5px dashed var(--orange); width: 92px; margin: 0 auto 3px; }
  .signature-value { font-family: "Crimson Text", serif; font-weight: 700; font-size: 13.5px; color: var(--green); line-height: 1.1; }
  .signature-label { font-weight: 600; font-size: 9px; color: var(--navy); margin-top: 3px; }

  .accent-band {
    position: absolute; top: 357px; left: 0; width: 610px; height: 19px;
    background: linear-gradient(90deg, var(--band-start), #3a5fe0 50%, var(--band-end));
  }
  .motto { position: absolute; top: 388px; left: 0; right: 0; text-align: center; font-weight: 700; line-height: 1.2; }
  .motto-top { font-size: 16px; color: var(--navy); letter-spacing: .4px; }
  .motto-bottom { font-size: 15.5px; color: var(--sky); letter-spacing: .4px; }
</style>
</head>
<body>

<div class="certificate certificate--primary">
  <div class="brand">
    <span class="brand-dot"></span>
    <div class="brand-name">BRAXLEY GUILD</div>
    <div class="brand-sub">OF COMMERCE &amp; TOURISM</div>
  </div>
  <div class="texture-band" role="img" aria-label="Textured band with orange, blue and green angular panels on silver"></div>
  <svg class="band-edge" viewBox="0 0 610 30" preserveAspectRatio="none">
    <polygon points="0,6 610,6 610,14 305,20 0,14" fill="var(--edge)"/>
  </svg>
  <div class="title-accent title-accent--left" role="img" aria-label="Orange decorative accent"></div>
  <div class="title-accent title-accent--right" role="img" aria-label="Blue decorative accent"></div>
  <div class="title">Certificate</div>
  <div class="subtitle">OF ANNUAL MEMBERSHIP</div>
  <div class="given-to">This Certificate is proudly given to</div>
  <div class="recipient">PROUD CHAMBER MEMBERS, 2022</div>
  <div class="signature signature--left">
    <div class="signature-line"></div>
    <div class="signature-value">Name Here</div>
    <div class="signature-label">Advocate</div>
  </div>
  <div class="signature signature--right">
    <div class="signature-line"></div>
    <div class="signature-value">01.01.2022</div>
    <div class="signature-label">Date</div>
  </div>
  <div class="accent-band"></div>
  <div class="motto">
    <div class="motto-top">WORKING TOGETHER</div>
    <div class="motto-bottom">FOR A STRONGER COMMUNITY</div>
  </div>
</div>

<div class="certificate certificate--secondary">
  <div class="brand">
    <span class="brand-dot"></span>
    <div class="brand-name">BRAXLEY GUILD</div>
    <div class="brand-sub">OF COMMERCE &amp; TOURISM</div>
  </div>
  <div class="texture-band" role="img" aria-label="Textured band with orange, blue and green angular panels on silver"></div>
  <svg class="band-edge" viewBox="0 0 610 30" preserveAspectRatio="none">
    <polygon points="0,6 610,6 610,14 305,20 0,14" fill="var(--edge)"/>
  </svg>
  <div class="title-accent title-accent--left" role="img" aria-label="Orange decorative accent"></div>
  <div class="title-accent title-accent--right" role="img" aria-label="Blue decorative accent"></div>
  <div class="title">Certificate</div>
  <div class="subtitle">OF ANNUAL MEMBERSHIP</div>
  <div class="given-to">This Certificate is proudly given to</div>
  <div class="recipient">PROUD CHAMBER MEMBERS, 2022</div>
  <div class="signature signature--left">
    <div class="signature-line"></div>
    <div class="signature-value">Name Here</div>
    <div class="signature-label">Advocate</div>
  </div>
  <div class="signature signature--right">
    <div class="signature-line"></div>
    <div class="signature-value">01.01.2022</div>
    <div class="signature-label">Date</div>
  </div>
  <div class="accent-band"></div>
  <div class="motto">
    <div class="motto-top">WORKING TOGETHER</div>
    <div class="motto-bottom">FOR A STRONGER COMMUNITY</div>
  </div>
</div>

</body>
</html>
```